Multiple Page Flyer -6 pager

Looking for an attractive new flyer for our synthetic greens and turf division. Please use our new logo attached and theme around the logo and use lots of pictures from the website. Pick the best from

I envision the following:
Page 1: Cover page
Page 2: Golfing Greens
Page 3: Golfing Greens 2
Page 4: Artificial Lawns 50% / Pet Turf 50%
Page 5: Pet Turf 50% / Playgrounds 50%
Page 6: Sports

```html
<!DOCTYPE html>
<html lang="en">
<head>
<meta charset="utf-8">
<title>Sports Turf Flyer – Page 6</title>
<link href="https://fonts.googleapis.com/css2?family=Source+Sans+3:wght@400&display=swap" rel="stylesheet">
<style>
  :root {
    --backdrop: #4f6465;
    --ink: #141414;
    --sage: #c3d2a5;
    --mist: #f7f9fa;
    --haze: #dde3e8;
    --frame-olive: #676d5d;
    --frame-gray: #8a8d8e;
    --photo-border: #111;
    --turf-deep: #2f8a1a;
    --turf-bright: #55c428;
    --photo-green: #3f9a2a;
    --photo-light: #5cc62c;
  }
  * { margin: 0; padding: 0; box-sizing: border-box; }
  html, body {
    width: 1200px; height: 1200px; overflow: hidden;
    background: var(--backdrop);
  }
  .flyer-page {
    position: absolute; left: 204px; top: 40px;
    width: 792px; height: 1120px; overflow: hidden;
    background:
      radial-gradient(ellipse 70% 55% at 62% 42%, var(--mist) 0%, rgba(247,249,250,0.85) 40%, rgba(247,249,250,0) 80%),
      linear-gradient(100deg, var(--sage) 0%, #d4dec0 35%, #e8ecef 65%, var(--haze) 100%);
  }
  .intro-copy {
    position: absolute; left: 75px; top: 81px; width: 710px;
    font-family: "Source Sans 3", sans-serif;
    font-size: 15.8px; line-height: 21.3px; color: var(--ink);
    white-space: nowrap;
  }
  .intro-copy p + p { margin-top: 21.3px; }
  .drop-cap {
    position: absolute; left: 75px; top: 62px;
    font-family: "Source Sans 3", sans-serif;
    font-size: 66px; line-height: 66px; color: var(--ink);
  }
  .indent-1 { padding-left: 41px; }
  .indent-2 { padding-left: 51px; }
  .turf-band {
    position: absolute; left: 0; right: 0; top: 875px; bottom: 0;
    background: linear-gradient(180deg, var(--turf-deep), var(--turf-bright));
  }
  .photo-frame {
    position: absolute; left: 88px; top: 530px; width: 651px; height: 345px;
    background: linear-gradient(90deg, var(--frame-olive) 0 24px, #9a9d97 24px, var(--frame-gray));
  }
  .sports-photo {
    position: absolute; left: 112px; top: 533px; width: 615px; height: 467px;
    border: 3px solid var(--photo-border); border-left-width: 6px;
    background: linear-gradient(180deg, var(--photo-green), var(--photo-light));
  }
</style>
</head>
<body>
  <main class="flyer-page">
    <span class="drop-cap">A</span>
    <section class="intro-copy">
      <p><span class="indent-1">rtificial turf was born on the sports field, and that’s where it continues to do its best work.</span><br>
      <span class="indent-2">However, the high-tech, environmentally friendly, and amazingly realistic artificial lawns</span><br>
      of today bear little resemblance to the artificial turf of yesterday. At Summit Ridge Turf, we<br>
      install the best quality artificial lawns available for sports fields and more.</p>
      <p>In our unpredictable Wisconsin weather, many a sporting event has been delayed or canceled due to<br>
      poor field conditions. An unexpected storm rolls through, and a planned weekend of sports excitement<br>
      is ruined. Traditional grass sports fields are subject to all kinds of damage – and the ensuing cleanup<br>
      costs – that our advanced artificial lawn materials are simply immune to.</p>
      <p>Our premier synthetic turf is the perfect solution to keeping your athletic fields looking great year<br>
      round. We specialize in soccer fields, baseball fields, football fields, lacrosse fields, bocce courts and<br>
      more (we also do golf greens). Our synthetic grass and lawn products are an excellent choice for high<br>
      traffic, heavy usage areas where low maintenance and water conservation is desired.</p>
      <p>Athletes know that the playing surface can determine the performance of the team and thus the<br>
      outcome of the game. Win or lose, the players depend on the surface to be safe, reliable, and familiar.<br>
      Summit Ridge Turf understands the demands of today’s athletes, and we install a product built<br>
      to respond to their needs, and durable enough to hold up to hours of use and abuse.</p>
    </section>
    <div class="turf-band" role="img" aria-label="Close-up texture of green synthetic grass blades"></div>
    <div class="photo-frame"></div>
    <div class="sports-photo" role="img" aria-label="Indoor batting facility with green synthetic turf and a batter at home plate"></div>
  </main>
</body>
</html>
```